Velmora Consulting Business

** Please add the content information from my old business card
1. I would like to see a two sided business card with both options with the 1st Option--Tallow Spire-new WHITE BACKGROUND LOGO
2 nd Option-Tallow Spire - new BLACK- Background Logo
3rd -Option a business card with my Photo on the card
Please add the new word to the card information:
EXECUTION
AS THE OWNER'S REP
WE AIM TO ACHIEVE YOUR
INFRASTRUCTURE VISION with
OUR SPECIALIZATION & EXECUTION in:

FUNDING Planning
BUSINESS Planning
INFRASTRUCTURE Planning
PROJECT Management
Since 2012
_____________________________________________________________________
I want to get spot uv raised printing. I was liking a a nice rich white linen paper stock with black writing & NOT A COLORED CARD other than a variety of white or black cards concept

```html
<!DOCTYPE html>
<html lang="en">
<head>
<meta charset="utf-8">
<title>Velmora Consulting – Business Card</title>
<link href="https://fonts.googleapis.com/css2?family=Open+Sans:wght@400;600;700;800&display=swap" rel="stylesheet">
<style>
  :root {
    --backdrop: #222223;
    --card: #1f1f21;
    --card-deep: #0d0d0e;
    --red: #d71f2c;
    --red-dark: #a8141f;
    --white: #ffffff;
    --muted: #e4e4e4;
  }
  * { box-sizing: border-box; margin: 0; padding: 0; }
  html, body {
    width: 1200px; height: 780px; overflow: hidden;
    background: var(--backdrop);
    font-family: "Open Sans", Arial, sans-serif;
  }
  .sheet {
    width: 1200px; height: 780px;
    display: flex; align-items: center; justify-content: center; gap: 28px;
  }
  .card {
    position: relative; width: 560px; height: 320px;
    background: var(--card); overflow: hidden;
    box-shadow: 0 14px 30px rgba(0,0,0,.55);
  }

  /* Front */
  .brand {
    position: absolute; display: flex; align-items: center; gap: 8px;
    color: var(--white); font-weight: 800; letter-spacing: .5px;
  }
  .brand__mark { width: 10px; height: 10px; background: var(--red); }
  .front .brand { left: 64px; top: 34px; font-size: 26px; }
  .front .brand__sub {
    position: absolute; left: 66px; top: 70px;
    color: var(--white); font-size: 9px; letter-spacing: 7px; text-transform: uppercase;
  }
  .person { position: absolute; left: 40px; top: 100px; padding-left: 14px; }
  .person::before {
    content: ""; position: absolute; left: 0; top: 4px; width: 7px; height: 28px; background: var(--red);
  }
  .person__name { color: var(--red); font-size: 22px; font-weight: 700; line-height: 1.3; }
  .person__title { color: var(--white); font-size: 11px; letter-spacing: .5px; margin-top: 2px; }
  .contact { position: absolute; left: 40px; top: 178px; list-style: none; }
  .contact li {
    display: flex; align-items: center; gap: 8px;
    color: var(--white); font-size: 12.5px; line-height: 21px;
  }
  .contact svg { width: 11px; height: 11px; fill: var(--red); }
  .contact .locations { margin-top: 6px; }
  .dot { display: inline-block; width: 6px; height: 6px; border-radius: 50%; background: var(--red); margin: 0 6px 1px; }
  .front__art { position: absolute; inset: 0; width: 100%; height: 100%; }

  /* Back */
  .back .brand { left: 44px; top: 92px; font-size: 28px; }
  .back .brand__sub {
    position: absolute; left: 46px; top: 132px;
    color: var(--white); font-size: 9px; letter-spacing: 7px; text-transform: uppercase;
  }
  .back__panel {
    position: absolute; left: 0; top: 0; width: 270px; height: 230px;
    background: linear-gradient(135deg, var(--card-deep), #2a2a2c);
  }
  .pitch {
    position: absolute; right: 26px; top: 44px; width: 280px; text-align: center;
    color: var(--white); text-transform: uppercase;
  }
  .pitch__lead { font-size: 11px; line-height: 17px; letter-spacing: .4px; }
  .services { list-style: none; margin-top: 12px; text-transform: none; font-size: 13px; line-height: 18px; }
  .services b { font-weight: 800; text-transform: uppercase; }
  .services .accent { color: var(--red); }
  .since { margin-top: 22px; color: var(--red); font-size: 13px; text-transform: none; }
</style>
</head>
<body>
<main class="sheet">

  <section class="card front">
    <svg class="front__art" viewBox="0 0 560 320" aria-hidden="false">
      <defs>
        <radialGradient id="portraitTone" cx="62%" cy="45%" r="60%">
          <stop offset="0" stop-color="#3a2a22"/>
          <stop offset="0.45" stop-color="#1a1616"/>
          <stop offset="1" stop-color="#060606"/>
        </radialGradient>
      </defs>
      <path d="M560 86 C450 88 330 170 300 320 L560 320 Z" fill="var(--red)"/>
      <path d="M560 96 C456 100 344 180 314 320 L560 320 Z" fill="var(--red-dark)"/>
      <path d="M560 102 C462 108 352 186 324 320 L560 320 Z" fill="url(#portraitTone)"
            role="img" aria-label="Portrait photograph of the lead project manager"/>
    </svg>

    <div class="brand"><span>Velmora</span><span class="brand__mark"></span></div>
    <div class="brand__sub">Consulting</div>

    <div class="person">
      <h1 class="person__name">Marguerite Holloway-Dane</h1>
      <p class="person__title">CEO / LEAD PROJECT MANAGER</p>
    </div>

    <ul class="contact">
      <li><svg viewBox="0 0 24 24"><path d="M6.6 10.8a15 15 0 0 0 6.6 6.6l2.2-2.2c.3-.3.7-.4 1-.2 1.1.4 2.3.6 3.6.6.6 0 1 .4 1 1V20c0 .6-.4 1-1 1A17 17 0 0 1 3 4c0-.6.4-1 1-1h3.5c.6 0 1 .4 1 1 0 1.3.2 2.5.6 3.6.1.3 0 .7-.2 1z"/></svg>867.555.0148</li>
      <li><svg viewBox="0 0 24 24"><path d="M2 5h20v14H2z M3 6l9 7 9-7" fill="none" stroke="var(--red)" stroke-width="2.4"/></svg>mara@velmora.ca</li>
      <li><svg viewBox="0 0 24 24"><circle cx="12" cy="12" r="9" fill="none" stroke="var(--red)" stroke-width="2.4"/><path d="M3 12h18M12 3c3 3 3 15 0 18M12 3c-3 3-3 15 0 18" fill="none" stroke="var(--red)" stroke-width="2"/></svg>www.velmora.ca</li>
      <li class="locations">Northpoint NT<span class="dot"></span>Eastvale NB</li>
    </ul>
  </section>

  <section class="card back">
    <div class="back__panel"></div>
    <div class="brand"><span>Velmora</span><span class="brand__mark"></span></div>
    <div class="brand__sub">Consulting</div>

    <div class="pitch">
      <p class="pitch__lead">As the owner's rep<br>we aim to achieve your<br>infrastructure vision with<br>our specialization &amp; execution in:</p>
      <ul class="services">
        <li><b>Funding</b> Planning</li>
        <li class="accent"><b>Business</b> Planning</li>
        <li><b>Project</b> Management</li>
        <li class="accent"><b>Infrastructure</b> Planning</li>
      </ul>
      <p class="since">Since 2012</p>
    </div>
  </section>

</main>
</body>
</html>
```